Flyer Vacation Gift Certificate

I need to create a beautiful flyer 8.5 x 11 PDF format flyer design. <br/><br/>Instructions:<br/>The flyer will really be a gift voucher for a las vegas vacation getaway. So must have a Las Vegas Theme exciting fun<br/><br/>The voucher should have two modules that will be editable. <br/>Must have a "Compliments Of" area and also must have an "Exclusively For" area<br/><br/>Keep in mind that this flyer will be printed so keep that in mind :)<br/><br/>Here the is the content for the vacation voucher:<br/><br/>There is no doubt that Las Vegas is one of the hottest travel destinations around the world. In fact, some people would even go as far as<br/>saying that perhaps it is THE hottest place to visit. Enjoy up to 4 nights of resort/casino accommodations in exciting Las Vegas, NV. Millions of people travel to this exciting city each year to enjoy its thrills. Thanks to the business you received this certificate from, now you can enjoy exciting Las Vegas, NV too!<br/><br/>Features:<br/>*Travel 7 Days A Week<br/>*Stay Your Choice Of Nights (1-4 Nights)<br/>*Good For Two Adults & Two Children<br/>*Pay Just The Taxes & Fees<br/>*Multiple Travel Date Requests Allowed<br/>*Fully Transferable To Another Person<br/>*Just A 30 Days Advance Notice Required<br/>*You Will Have 12 Months To Complete Travel After Redemption<br/><br/>HOW CAN WE DO THIS?<br/><br/>We contract with the world leading hotel chains and resorts to help them fill their otherwise empty rooms.<br/><br/>We help fill empty rooms which the hotels, resorts and cruise lines turn into additional revenue from other areas of their property and future bookings.<br/><br/>Hotels rarely experience full occupancy, yet they remain open, providing rooms and services at fixed costs. So when hotels give out their rooms by partnering with marketing companies like us, they might miss out on the room fee, but they already didn't have that in the first place, at least now they have the opportunity to gain a customer for their in-house restaurants, room service, their casinos, an extra day stay, future bookings, etc.<br/><br/>VIEW ALL THE DETAILS OF THIS SPECIAL OFFER AND REDEEM ONLINE AT <br/>WWW.QOTAVERNIX.COM<br/><br/>Certificate ID # 47261-38157<br/>Expires 02/29/2020<br/><br/><br/>*terms and conditions apply see website for details<br/><br/>KEEP IN MIND THE EXAMPLES I AM UPLOADING ARE SIMPLY TO SHOW YOU THAT THEY CONTAIN THE "COMPLIMENTS OF" AND "EXCLUSIVELY FOR" ELEMENTS. THESE MUST BE INCLUDED IN NEW DESIGN. PLEASE ONLY USE THE CONTENT I PROVIDED IN BRIEF, DONT USE CONTENT FROM EXAMPLES.

Target Market(s)

CONSUMERS THAT HAVE BEEN REWARDED WITH A VACATION CERTIFICATE FOR DOING BUSINESS WITH A COMPANY.

COMPANIES USE THESE AS MARKETING INCENTIVES TO ATTRACT MORE CUSTOMERS AND TO REWARD LOYALTY, ETC.

Industry/Entity Type

Travel Industry

Colors

Designer to choose colors to be used in the design.

Requirements
Must have
• I need to create a beautiful flyer 8.5 x 11 PDF format flyer design.
• Instructions:
• The flyer will really be a gift voucher for a las vegas vacation getaway. So must have a Las Vegas Theme exciting fun
• The voucher should have two modules that will be editable.
• Must have a "Compliments Of" area and also must have an "Exclusively For" area
• Keep in mind that this flyer will be printed so keep that in mind :)
• Here the is the content for the vacation voucher:
• There is no doubt that Las Vegas is one of the hottest travel destinations around the world. In fact, some people would even go as far as
• saying that perhaps it is THE hottest place to visit. Enjoy up to 4 nights of resort/casino accommodations in exciting Las Vegas, NV. Millions of people travel to this exciting city each year to enjoy its thrills. Thanks to the business you received this certificate from, now you can enjoy exciting Las Vegas, NV too!
• Features:
• *Travel 7 Days A Week
• *Stay Your Choice Of Nights (1-4 Nights)
• *Good For Two Adults & Two Children
• *Pay Just The Taxes & Fees
• *Multiple Travel Date Requests Allowed
• *Fully Transferable To Another Person
• *Just A 30 Days Advance Notice Required
• *You Will Have 12 Months To Complete Travel After Redemption
• HOW CAN WE DO THIS?
• We contract with the world leading hotel chains and resorts to help them fill their otherwise empty rooms.
• We help fill empty rooms which the hotels, resorts and cruise lines turn into additional revenue from other areas of their property and future bookings.
• Hotels rarely experience full occupancy, yet they remain open, providing rooms and services at fixed costs. So when hotels give out their rooms by partnering with marketing companies like us, they might miss out on the room fee, but they already didn't have that in the first place, at least now they have the opportunity to gain a customer for their in-house restaurants, room service, their casinos, an extra day stay, future bookings, etc.
• VIEW ALL THE DETAILS OF THIS SPECIAL OFFER AND REDEEM ONLINE AT
• WWW.QOTAVERNIX.COM
• Certificate ID # 47261-38157
• Expires 02/29/2020
• *terms and conditions apply see website for details
• KEEP IN MIND THE EXAMPLES I AM UPLOADING ARE SIMPLY TO SHOW YOU THAT THEY CONTAIN THE "COMPLIMENTS OF" AND "EXCLUSIVELY FOR" ELEMENTS. THESE MUST BE INCLUDED IN NEW DESIGN. PLEASE ONLY USE THE CONTENT I PROVIDED IN BRIEF, DONT USE CONTENT FROM EXAMPLES.
Nice to have
• EXCITING LAS VEGAS IMAGES THAT MAKE SOMEONE WANT TO GO THERE

```html
<!DOCTYPE html>
<html lang="en">
<head>
<meta charset="utf-8">
<title>Las Vegas Vacation Certificate</title>
<link href="https://fonts.googleapis.com/css2?family=Bebas+Neue&family=Roboto:ital,wght@0,400;0,500;0,700;1,500&family=Roboto+Condensed:wght@700&display=swap" rel="stylesheet">
<style>
  :root {
    --cyan: #12eef0;
    --red: #e42a2a;
    --ink: #0a0812;
    --white: #ffffff;
    --gray-top: #3a3a3a;
    --gray-mid: #4e4e4e;
    --text-soft: #eaeaea;
    --frame: #8a7a52;
  }
  * { margin: 0; padding: 0; box-sizing: border-box; }
  html, body { width: 927px; height: 1200px; overflow: hidden; background: #fff; }
  .flyer {
    position: relative; width: 927px; height: 1200px; overflow: hidden;
    font-family: 'Roboto', sans-serif; color: var(--white);
    background: radial-gradient(ellipse at 50% 40%, var(--gray-mid) 0%, var(--gray-top) 75%);
  }
  .hero {
    position: absolute; left: 0; top: 0; width: 927px; height: 350px;
    background: linear-gradient(180deg, #2f5ea0 0%, #4a7ab8 22%, #6b5a7a 45%, #5a3e3a 62%, #c48a3a 80%, #23314a 100%);
  }
  .compliments {
    position: absolute; left: 645px; top: 51px; width: 231px; height: 232px;
    background: var(--white); color: #111; text-align: center;
  }
  .compliments h2 {
    font-family: 'Roboto Condensed', sans-serif; font-weight: 700;
    font-size: 19px; line-height: 20px; margin-top: 25px;
  }
  .compliments .courtesy {
    position: absolute; left: 0; right: 0; top: 157px;
    font-weight: 500; font-size: 16.5px; line-height: 20px;
  }
  .exclusive {
    position: absolute; left: 0; top: 316px; width: 357px; height: 34px;
    background: var(--red); font-weight: 700; font-size: 16px;
    line-height: 34px; padding-left: 36px; white-space: nowrap;
  }
  .title-band {
    position: absolute; left: 0; top: 350px; width: 927px; height: 86px;
    background: var(--ink); text-align: center;
  }
  .title-band h1 {
    color: var(--cyan); font-weight: 700; font-size: 38px; line-height: 37px;
    letter-spacing: 1px; padding-top: 6px;
  }
  .intro { position: absolute; left: 70px; width: 787px; top: 458px; text-align: center; }
  .intro h3 {
    font-family: 'Roboto Condensed', sans-serif; font-weight: 700;
    font-size: 26px; line-height: 27px; letter-spacing: -0.5px;
  }
  .intro p { font-size: 16.5px; line-height: 21.2px; margin-top: 8px; color: var(--text-soft); }
  .gallery .photo {
    position: absolute; top: 624px; width: 226px; height: 174px;
    border: 3px solid var(--frame); box-shadow: 0 8px 10px rgba(0,0,0,.45);
  }
  .photo.sign { left: 108px; background: radial-gradient(circle at 50% 40%, #d2405a 0%, #3a1e3e 45%, #07070c 100%); }
  .photo.hotel { left: 350px; background: linear-gradient(160deg, #10131e 0%, #c8c8d2 40%, #e07a5a 75%, #3a1a20 100%); }
  .photo.strip { left: 592px; background: linear-gradient(180deg, #0b0d16 0%, #3a2a40 45%, #c84a3a 80%, #1a1a1a 100%); }
  .features { position: absolute; left: 70px; top: 826px; width: 390px; }
  .section-head { font-family: 'Bebas Neue', sans-serif; color: var(--cyan); font-size: 36px; line-height: 36px; }
  .features ul { list-style: none; margin-top: 11px; }
  .features li {
    font-size: 13px; line-height: 21.3px; color: var(--text-soft);
    display: flex; align-items: center; white-space: nowrap;
  }
  .features li svg { margin: 0 10px 0 2px; flex: none; }
  .divider { position: absolute; left: 463px; top: 818px; width: 1.5px; height: 232px; background: var(--cyan); }
  .how { position: absolute; left: 482px; top: 822px; width: 370px; }
  .how .point { display: flex; margin-top: 8px; }
  .how .point:first-of-type { margin-top: 6px; }
  .how .point svg { flex: none; margin-right: 4px; margin-top: 1px; }
  .how .point p { font-size: 11.7px; line-height: 13.5px; color: var(--text-soft); }
  .cta {
    position: absolute; left: 0; width: 927px; top: 1062px; text-align: center;
    color: var(--cyan); font-style: italic; font-weight: 500; font-size: 25px; line-height: 28px;
  }
  .footer-band { position: absolute; left: 0; top: 1136px; width: 927px; height: 64px; background: var(--ink); }
  .corner { position: absolute; left: 0; top: 0; }
  .cert-info {
    position: absolute; left: 620px; width: 262px; top: 1124px;
    text-align: center; font-weight: 700;
  }
  .cert-info .line { font-size: 14.5px; line-height: 17px; }
  .cert-info .terms { font-size: 11px; line-height: 15px; letter-spacing: -0.4px; }
</style>
</head>
<body>
<div class="flyer">
  <div class="hero" role="img" aria-label="Las Vegas Strip skyline at dusk with lit resort towers and fountains"></div>

  <div class="compliments">
    <h2>THIS CERTIFICATE IS<br>COMPLIMENTS OF</h2>
    <div class="courtesy">Certificate Courtesy Of<br>Text Line 2<br>Text Line 3</div>
  </div>

  <div class="exclusive">EXCLUSIVELY FOR : CUSTOMER NAME</div>

  <div class="title-band">
    <h1>4 Nights Of Resort Casino Accommodations<br>In Las Vegas, NV!</h1>
  </div>

  <div class="intro">
    <h3>There is no doubt that Las Vegas is one of the hottest<br>travel destinations around the world.</h3>
    <p>In fact, some people would even go as far as saying that perhaps it is THE hottest place to visit. Enjoy up to 4 nights of resort/casino accommodations in exciting Las Vegas, NV. Millions of people travel to this exciting city each year to enjoy its thrills. Thanks to the business you received this certificate from, now you can enjoy exciting Las Vegas, NV too!</p>
  </div>

  <div class="gallery">
    <div class="photo sign" role="img" aria-label="Illuminated welcome sign at night with palm trees"></div>
    <div class="photo hotel" role="img" aria-label="Resort hotel tower with neon facade at night"></div>
    <div class="photo strip" role="img" aria-label="Busy boulevard of casinos and traffic lights at night"></div>
  </div>

  <div class="features">
    <div class="section-head">FEATURES:</div>
    <ul>
      <li><svg width="10" height="10" viewBox="0 0 10 10"><rect x="0.7" y="0.7" width="8.6" height="8.6" fill="none" stroke="#d8d8d8" stroke-width="1.2"/><rect x="2.8" y="2.8" width="4.4" height="4.4" fill="#d8d8d8"/></svg>Travel 7 Days A Week</li>
      <li><svg width="10" height="10" viewBox="0 0 10 10"><rect x="0.7" y="0.7" width="8.6" height="8.6" fill="none" stroke="#d8d8d8" stroke-width="1.2"/><rect x="2.8" y="2.8" width="4.4" height="4.4" fill="#d8d8d8"/></svg>Stay Your Choice Of Nights (1-4 Nights)</li>
      <li><svg width="10" height="10" viewBox="0 0 10 10"><rect x="0.7" y="0.7" width="8.6" height="8.6" fill="none" stroke="#d8d8d8" stroke-width="1.2"/><rect x="2.8" y="2.8" width="4.4" height="4.4" fill="#d8d8d8"/></svg>Good For Two Adults &amp; Two Children</li>
      <li><svg width="10" height="10" viewBox="0 0 10 10"><rect x="0.7" y="0.7" width="8.6" height="8.6" fill="none" stroke="#d8d8d8" stroke-width="1.2"/><rect x="2.8" y="2.8" width="4.4" height="4.4" fill="#d8d8d8"/></svg>Pay Just The Taxes &amp; Fees</li>
      <li><svg width="10" height="10" viewBox="0 0 10 10"><rect x="0.7" y="0.7" width="8.6" height="8.6" fill="none" stroke="#d8d8d8" stroke-width="1.2"/><rect x="2.8" y="2.8" width="4.4" height="4.4" fill="#d8d8d8"/></svg>Multiple Travel Date Requests Allowed</li>
      <li><svg width="10" height="10" viewBox="0 0 10 10"><rect x="0.7" y="0.7" width="8.6" height="8.6" fill="none" stroke="#d8d8d8" stroke-width="1.2"/><rect x="2.8" y="2.8" width="4.4" height="4.4" fill="#d8d8d8"/></svg>Fully Transferable To Another Person</li>
      <li><svg width="10" height="10" viewBox="0 0 10 10"><rect x="0.7" y="0.7" width="8.6" height="8.6" fill="none" stroke="#d8d8d8" stroke-width="1.2"/><rect x="2.8" y="2.8" width="4.4" height="4.4" fill="#d8d8d8"/></svg>Just A 30 Days Advance Notice Required</li>
      <li><svg width="10" height="10" viewBox="0 0 10 10"><rect x="0.7" y="0.7" width="8.6" height="8.6" fill="none" stroke="#d8d8d8" stroke-width="1.2"/><rect x="2.8" y="2.8" width="4.4" height="4.4" fill="#d8d8d8"/></svg>You Will Have 12 Months To Complete Travel After Redemption</li>
    </ul>
  </div>

  <div class="divider"></div>

  <div class="how">
    <div class="section-head">HOW CAN WE DO THIS?</div>
    <div class="point">
      <svg width="24" height="22" viewBox="0 0 24 22" fill="none" stroke="#12eef0" stroke-width="1.3"><rect x="1" y="7" width="4" height="12"/><path d="M5 9 L10 5 L12 2 L14 3 L13 7 L23 7 L23 9.5 L15 9.5 M19 9.5 L19 12 L15 12 M18 12 L18 14.5 L14 14.5 M17 14.5 L17 17 L9 17 L5 16"/></svg>
      <p>We contract with the world leading hotel chains and resorts to help them fill their otherwise empty rooms.</p>
    </div>
    <div class="point">
      <svg width="24" height="22" viewBox="0 0 24 22" fill="none" stroke="#12eef0" stroke-width="1.3"><rect x="1" y="7" width="4" height="12"/><path d="M5 9 L10 5 L12 2 L14 3 L13 7 L23 7 L23 9.5 L15 9.5 M19 9.5 L19 12 L15 12 M18 12 L18 14.5 L14 14.5 M17 14.5 L17 17 L9 17 L5 16"/></svg>
      <p>We help fill empty rooms which the hotels, resorts and cruise lines turn into additional revenue from other areas of their property and future bookings.</p>
    </div>
    <div class="point">
      <svg width="24" height="22" viewBox="0 0 24 22" fill="none" stroke="#12eef0" stroke-width="1.3"><rect x="1" y="7" width="4" height="12"/><path d="M5 9 L10 5 L12 2 L14 3 L13 7 L23 7 L23 9.5 L15 9.5 M19 9.5 L19 12 L15 12 M18 12 L18 14.5 L14 14.5 M17 14.5 L17 17 L9 17 L5 16"/></svg>
      <p>Hotels rarely experience full occupancy, yet they remain open, providing rooms and services at fixed costs. So when hotels give out their rooms by partnering with marketing companies like us, they might miss out on the room fee, but they already didn't have that in the first place, at least now they have the opportunity to gain a customer for their in-house restaurants, room service, their casinos, an extra day stay, future bookings, etc.</p>
    </div>
  </div>

  <div class="cta">View all the details of this special offer and Redeem online at<br>www.Qotavernix.com</div>

  <div class="footer-band"></div>
  <svg class="corner" width="927" height="1200" viewBox="0 0 927 1200"><polygon points="634,1113 927,1113 927,1200 557,1200" fill="#e42a2a"/></svg>

  <div class="cert-info">
    <div class="line">CERTIFICATE ID # 47261-38157</div>
    <div class="line">EXPIRES 02/29/2020</div>
    <div class="terms">(Terms and conditions apply see website for details)</div>
  </div>
</div>
</body>
</html>
```